Mark Tolvane actor business cards

I need unique and interesting business cards that have my headshot photo, my name, tagline/position/skills, contact info, preferred pronouns (he, him, his), and social media handles. These need to be memorable networking tools to hand out at events that stand out. I am an actor that works in theatre, film, and TV and usually play darker dramatic roles, though it doesn't have to necessarily need to be reflected in the design, but I am not a light, comedic actor. In my email tagline, My position/skills are "Actor, storyteller, theatre maker."

Target Market(s)

Casting directors, film and television community, theatre community.

Industry/Entity Type

Performing Art

Contact Information for Business Card

Mark Tolvane. Pronouns: he, him, his. Contact info: (555)-318-7064, Marktolvane.example, marktolvane@postbox.example. Talent representation: Kirwood Talent Agency. Social Media: Facebook page, twitter and instagram: @MarkTolvanePlays. Company Member of Harbin Theatre Company.

Font styles to use
Serif
Decorative

Colors

Designer to choose colors to be used in the design.

Requirements
Must have
• Headshot photo, name, tagline, preferred pronouns, contact info, Social media handle, talent agency logo, harbin theatre company logo. Both logos should be smaller than my name. Under or near Harbin logo, it should say "Company Member"
Nice to have
• I would like to have the photo, my name, tagline, and maybe pronouns on one side, and all contact info, and social media, and talent agency logo on the other. I would like the style to reflect my type which is a little more serious and somewhat darker, and definitely not comedic.
Should not have
• No extraneous theatre lights, camera, or film, etc. clip art or photos. Use solid backgrounds or photos provided.

```html
<!DOCTYPE html>
<html lang="en">
<head>
<meta charset="utf-8">
<title>Mark Tolvane – Business Cards</title>
<link rel="stylesheet" href="https://fonts.googleapis.com/css2?family=Cormorant+Garamond:ital,wght@1,600&family=Open+Sans:wght@400;600&display=swap">
<style>
  :root {
    --bg: #e7e5e2;
    --white: #ffffff;
    --ink: #111111;
    --card-black: #0d0d0d;
    --blue: #2196d9;
    --teal: #1f86b5;
    --rule: #5a5a5a;
    --light-text: #f2f2f2;
    --shirt: #5b6fae;
    --photo-light: #c9d0e2;
  }
  * { margin: 0; padding: 0; box-sizing: border-box; }
  html, body { width: 1200px; height: 900px; overflow: hidden; }
  body {
    background: var(--bg);
    font-family: "Open Sans", Arial, sans-serif;
    display: flex;
    flex-direction: column;
    align-items: center;
    justify-content: center;
    gap: 40px;
  }
  .card {
    position: relative;
    width: 700px;
    height: 400px;
    overflow: hidden;
    box-shadow: 0 6px 18px rgba(0,0,0,.18);
  }

  /* Front */
  .card--front { background: var(--white); }
  .card__shapes { position: absolute; inset: 0; }
  .headshot {
    position: absolute;
    left: 350px; top: 120px;
    width: 340px; height: 222px;
    background: radial-gradient(ellipse at 55% 35%, var(--photo-light) 0%, #a8b3d2 35%, var(--shirt) 75%);
  }
  .front__name {
    position: absolute; left: 90px; top: 18px;
    font-family: "Cormorant Garamond", Georgia, serif;
    font-style: italic; font-weight: 600;
    font-size: 34px; color: var(--blue);
  }
  .front__tagline {
    position: absolute; left: 90px; top: 62px;
    font-size: 17px; color: var(--ink);
  }
  .agency {
    position: absolute; left: 70px; top: 140px;
    display: flex; align-items: center; gap: 12px;
  }
  .agency__mark { width: 26px; height: 26px; border-radius: 50%; background: var(--ink); }
  .agency__name { font-size: 22px; font-weight: 600; color: var(--ink); }
  .front__pronouns {
    position: absolute; left: 30px; top: 215px;
    font-family: "Cormorant Garamond", Georgia, serif;
    font-style: italic; font-weight: 600;
    font-size: 40px; color: var(--teal);
  }

  /* Back */
  .card--back {
    background: linear-gradient(160deg, #1c1c1c 0%, var(--card-black) 45%, #050505 100%);
    color: var(--light-text);
    text-align: center;
  }
  .back__content {
    position: absolute; inset: 0;
    display: flex; flex-direction: column; align-items: center; justify-content: center;
  }
  .back__name {
    font-family: "Cormorant Garamond", Georgia, serif;
    font-style: italic; font-weight: 600;
    font-size: 34px; line-height: 1.1;
  }
  .back__tagline { font-size: 16px; margin-top: 2px; }
  .divider {
    display: flex; align-items: center; gap: 6px;
    width: 300px; margin: 12px 0 8px;
  }
  .divider::before, .divider::after {
    content: ""; flex: 1; height: 1px; background: var(--rule);
  }
  .icon-dot {
    width: 20px; height: 20px; border-radius: 50%;
    background: var(--light-text);
    display: flex; align-items: center; justify-content: center;
  }
  .social-dot { width: 22px; height: 22px; border-radius: 50%; background: var(--light-text); }
  .contact { font-size: 17px; line-height: 1.3; }
  .handle { font-size: 17px; }
</style>
</head>
<body>

  <section class="card card--front" aria-label="Card front">
    <svg class="card__shapes" width="700" height="400" viewBox="0 0 700 400" aria-hidden="true">
      <polygon points="22,18 60,18 22,52" fill="var(--blue)"/>
      <polygon points="62,22 82,22 82,60 36,60" fill="var(--ink)"/>
      <polygon points="0,268 430,322 420,338 0,290" fill="var(--blue)"/>
      <polygon points="440,342 700,342 700,400 420,400" fill="var(--ink)"/>
    </svg>
    <div class="headshot" role="img" aria-label="Headshot of Mark Tolvane in a blue shirt"></div>
    <h1 class="front__name">Mark Tolvane</h1>
    <p class="front__tagline">Actor, Storyteller, Theatre Maker</p>
    <div class="agency">
      <span class="agency__mark"></span>
      <span class="agency__name">Kirwood Talent Agency</span>
    </div>
    <p class="front__pronouns">He, Him, His</p>
  </section>

  <section class="card card--back" aria-label="Card back">
    <div class="back__content">
      <h2 class="back__name">Mark Tolvane</h2>
      <p class="back__tagline">Actor, Storyteller, Theatre Maker</p>
      <div class="divider">
        <span class="icon-dot">
          <svg width="12" height="12" viewBox="0 0 12 12" aria-label="Phone"><path d="M3 1l2 2-1 1.5c.8 1.5 2 2.7 3.5 3.5L9 7l2 2-1.5 2C5 10.5 1.5 7 1 2.5z" fill="var(--card-black)"/></svg>
        </span>
        <span class="icon-dot">
          <svg width="12" height="12" viewBox="0 0 12 12" aria-label="Email"><rect x="1" y="3" width="10" height="7" fill="none" stroke="var(--card-black)" stroke-width="1.3"/><path d="M1 3l5 4 5-4" fill="none" stroke="var(--card-black)" stroke-width="1.3"/></svg>
        </span>
        <span class="icon-dot">
          <svg width="12" height="12" viewBox="0 0 12 12" aria-label="Website"><circle cx="6" cy="6" r="4.5" fill="none" stroke="var(--card-black)" stroke-width="1.2"/><path d="M1.5 6h9M6 1.5c-2 3-2 6 0 9M6 1.5c2 3 2 6 0 9" fill="none" stroke="var(--card-black)" stroke-width="1"/></svg>
        </span>
      </div>
      <p class="contact">(555)-318-7064</p>
      <p class="contact">marktolvane@postbox.example</p>
      <p class="contact">www.Marktolvane.example</p>
      <div class="divider">
        <span class="social-dot"></span>
        <span class="social-dot"></span>
        <span class="social-dot"></span>
      </div>
      <p class="handle">@MarkTolvanePlays</p>
    </div>
  </section>

</body>
</html>
```